Linden Medical - Flyer

We are a full service pharmacy that specializes in diabetic testing and medications. We research the patient's insurance to maximize their insurance benefit and then deliver the medications monthly directly to the patient's doorstep, for free! We save the patient, time and money every month.
We would love a flyer that we can distribute to Doctor's offices and patients that sum up our pharmacy. Emphasis on saving money, time, and getting the best quality supplies by maximizing their insurance. We want it to be eye catching, clean, and professional.
You can use our logo or feel free to make your own design.
diabetic patients wanting to save money
Insurance

```html
<!DOCTYPE html>
<html lang="en">
<head>
<meta charset="utf-8">
<title>Linden Medical – Flyer</title>
<link rel="stylesheet" href="https://fonts.googleapis.com/css2?family=Arimo:wght@400;700&display=swap">
<style>
  :root {
    --stage: #eef1f3;
    --sky-top: #a9dcea;
    --sky-mid: #e4f3f8;
    --paper: #ffffff;
    --ink: #1c1c1c;
    --teal: #1b9fb2;
    --leaf: #5aa427;
    --leaf-light: #8cc63f;
    --alert: #c8161d;
    --icon-red: #d22a26;
    --card-red: #b3141c;
    --brand: #2f3f46;
  }
  * { box-sizing: border-box; margin: 0; padding: 0; }
  html, body { width: 1200px; height: 1019px; overflow: hidden; }
  body {
    background: var(--stage);
    font-family: "Arimo", Arial, sans-serif;
    color: var(--ink);
    position: relative;
  }
  .panel {
    position: absolute;
    top: 165px;
    width: 541px;
    height: 701px;
    overflow: hidden;
    background:
      radial-gradient(circle at 30% 8%, rgba(255,255,255,.9) 0 60px, transparent 140px),
      radial-gradient(circle at 75% 30%, rgba(255,255,255,.8) 0 40px, transparent 150px),
      radial-gradient(circle at 20% 55%, rgba(255,255,255,.7) 0 30px, transparent 120px),
      linear-gradient(180deg, var(--sky-top) 0%, var(--sky-mid) 35%, #f4fafc 70%, var(--paper) 100%);
  }
  .panel--front { left: 57px; }
  .panel--back { left: 611px; }

  .swoosh { position: absolute; left: 0; bottom: 0; width: 541px; height: 240px; }

  .brand {
    position: absolute;
    display: flex;
    align-items: center;
    gap: 10px;
    font-weight: 400;
    color: var(--brand);
    letter-spacing: 1px;
    white-space: nowrap;
  }
  .brand__dot { width: 34px; height: 34px; border-radius: 50%; background: var(--leaf); flex: none; }
  .panel--front .brand { left: 0; right: 0; top: 40px; justify-content: center; font-size: 36px; }
  .panel--back .brand { left: 312px; top: 552px; font-size: 17px; gap: 6px; letter-spacing: .5px; }
  .panel--back .brand__dot { width: 18px; height: 18px; }

  .headline {
    position: absolute; left: 0; right: 0; top: 140px;
    text-align: center; font-size: 22px; line-height: 32px; font-weight: 400;
  }
  .headline .hl-green { color: var(--leaf); font-weight: 700; }
  .headline strong { font-weight: 700; }

  .benefit { position: absolute; display: flex; align-items: center; gap: 20px; }
  .benefit__icon {
    width: 68px; height: 68px; border-radius: 50%; flex: none;
    background: radial-gradient(circle at 50% 50%, #f3e1c6 0 20px, var(--icon-red) 21px);
  }
  .benefit__label { font-size: 19px; line-height: 23px; text-transform: uppercase; }
  .b1 { left: 74px; top: 236px; }
  .b2 { left: 288px; top: 236px; }
  .b3 { left: 74px; top: 341px; }
  .b4 { left: 288px; top: 341px; }
  .b2 .benefit__icon, .b4 .benefit__icon { background: radial-gradient(circle at 50% 50%, #9b6b3d 0 22px, var(--icon-red) 23px); }

  .art { position: absolute; }
  .art--fingers {
    left: 86px; top: 432px; width: 243px; height: 190px;
    background: linear-gradient(180deg, #e9b9a0 0%, #d99b80 60%, #c7836a 100%);
    border-radius: 40px 40px 8px 8px;
  }
  .art--figure {
    left: 92px; top: 414px; width: 176px; height: 210px;
    background: linear-gradient(180deg, #3a3a3a, #141414);
    border-radius: 60px 60px 10px 10px;
  }
  .art--heart {
    left: 7px; top: 596px; width: 82px; height: 82px;
    background: radial-gradient(circle at 45% 40%, #ef3a3a 0 28px, #5aa427 30px 40px, transparent 41px);
  }

  .gift {
    position: absolute; width: 190px; height: 118px;
    background: linear-gradient(160deg, #ffffff 0%, #eeeeee 100%);
    border-radius: 10px;
    box-shadow: 0 6px 12px rgba(0,0,0,.18);
    transform: rotate(-15deg);
  }
  .gift::after {
    content: ""; position: absolute; right: 0; bottom: 26px; width: 34px; height: 8px;
    background: var(--card-red); transform: skewY(-30deg);
  }
  .gift__title { position: absolute; right: 18px; top: 12px; font-size: 13px; color: var(--card-red); }
  .gift__amount { position: absolute; left: 60px; top: 32px; font-size: 42px; font-weight: 700; color: var(--card-red); }
  .gift__note { position: absolute; left: 40px; bottom: 14px; font-size: 10.5px; color: var(--ink); }
  .gift__bow {
    position: absolute; left: -22px; top: 28px; width: 46px; height: 46px;
    background: radial-gradient(circle, #e21f26 0 14px, #a8121a 15px 22px, transparent 23px);
  }
  .panel--front .gift { left: 336px; top: 480px; }
  .panel--back .gift { left: 320px; top: 365px; }

  .contact { position: absolute; left: 0; right: 0; text-align: center; color: #fff; white-space: nowrap; }
  .panel--front .contact--phone { top: 636px; font-size: 17px; font-weight: 700; }
  .panel--front .contact--phone b { font-size: 25px; }
  .panel--front .contact--web { top: 672px; font-size: 19px; }
  .panel--back .contact--phone { top: 660px; font-size: 26px; font-weight: 700; left: 50px; }
  .panel--back .contact--web { top: 586px; left: 292px; right: auto; font-size: 16px; color: var(--brand); }

  .service { position: absolute; left: 44px; right: 30px; font-size: 16px; line-height: 23px; }
  .service em { font-style: normal; color: var(--teal); font-weight: 700; font-size: 18px; }
  .s1 { top: 22px; } .s2 { top: 88px; } .s3 { top: 155px; } .s4 { top: 220px; }

  .cta { position: absolute; left: 44px; top: 300px; }
  .cta__title { font-size: 28px; font-weight: 700; color: var(--alert); }
  .cta__text { font-size: 17px; line-height: 23px; margin-top: 2px; }
</style>
</head>
<body>

<section class="panel panel--front" aria-label="Flyer front">
  <svg class="swoosh" viewBox="0 0 541 240" preserveAspectRatio="none" aria-hidden="true">
    <path d="M0 110 Q270 170 541 40 L541 240 L0 240 Z" fill="var(--leaf-light)"/>
    <path d="M0 125 Q280 190 541 70 L541 240 L0 240 Z" fill="var(--leaf)"/>
    <path d="M0 128 Q270 145 541 48 Q290 160 0 140 Z" fill="#ffffff" opacity=".8"/>
  </svg>

  <div class="brand"><span class="brand__dot"></span>LINDEN MEDICAL</div>

  <h1 class="headline">Are the costs of your <span class="hl-green">Diabetic Testings</span><br>upplies as high as your <strong>Blood Sugar?</strong></h1>

  <div class="benefit b1"><span class="benefit__icon" role="img" aria-label="Compass icon"></span><span class="benefit__label">Free<br>Meter</span></div>
  <div class="benefit b2"><span class="benefit__icon" role="img" aria-label="Wallet icon"></span><span class="benefit__label">Save<br>Money</span></div>
  <div class="benefit b3"><span class="benefit__icon" role="img" aria-label="Alarm clock icon"></span><span class="benefit__label">Save<br>Time</span></div>
  <div class="benefit b4"><span class="benefit__icon" role="img" aria-label="Delivery case icon"></span><span class="benefit__label">Free<br>Delivery</span></div>

  <div class="art art--fingers" role="img" aria-label="Photo of four fingers drawn as a smiling family"></div>

  <div class="gift">
    <span class="gift__bow" role="img" aria-label="Red gift bow"></span>
    <span class="gift__title">Gift Card</span>
    <span class="gift__amount">$20</span>
    <span class="gift__note">given your first order</span>
  </div>

  <p class="contact contact--phone">Toll Free Number <b>13579246</b></p>
  <p class="contact contact--web">www.lindenmedical-rx.com</p>
</section>

<section class="panel panel--back" aria-label="Flyer back">
  <svg class="swoosh" viewBox="0 0 541 240" preserveAspectRatio="none" aria-hidden="true">
    <path d="M0 57 Q200 185 541 150 L541 240 L0 240 Z" fill="var(--leaf-light)"/>
    <path d="M0 64 Q200 190 541 156 L541 170 Q220 205 0 100 Z" fill="#ffffff"/>
    <path d="M0 100 Q220 205 541 170 L541 240 L0 240 Z" fill="var(--leaf)"/>
  </svg>

  <p class="service s1">We are a full service pharmacy that specializes in <em>diabetic testing</em> supplies and oral medications.</p>
  <p class="service s2">We research <em>your insurance</em> to determine how to save you the most money</p>
  <p class="service s3">We then contact your physician to get the <em>appropriate authorization</em></p>
  <p class="service s4">We ship your testing supplies and oral medications directly to your home for <em>free!</em></p>

  <div class="cta">
    <h2 class="cta__title">Get started Today!</h2>
    <p class="cta__text">Call our toll free number OR go to our website<br>and fill our form.</p>
  </div>

  <div class="art art--figure" role="img" aria-label="Illustration of a man in a suit with arms raised"></div>

  <div class="gift">
    <span class="gift__bow" role="img" aria-label="Red gift bow"></span>
    <span class="gift__title">Gift Card</span>
    <span class="gift__amount">$20</span>
    <span class="gift__note">given your first order</span>
  </div>

  <div class="brand"><span class="brand__dot"></span>LINDEN MEDICAL</div>
  <p class="contact contact--web">www.lindenmedical-rx.com</p>

  <div class="art art--heart" role="img" aria-label="Red heart held in a green hand"></div>

  <p class="contact contact--phone">Toll Free Number 13579246</p>
</section>

</body>
</html>
```